RW Framewell Inc Business cards

We need business cards using our existing logo but slightly modified. Right now the logo says RW Loadbearing Masonry. We want to keep the RW part of the design, but replace the Structural Concrete portion with "FRAMEWELL". Please see the attached file.
Ideally this would be a blank template so we can add Different Names, titles, and phone numbers later.
On the one side we want only the logo and on the other side the detail. I'm attaching an example for you to see.
Please reach out with any other questions. Our address and other details will be given out once we find a design we like.

Target Market(s)

Construction Industry

```html
<!DOCTYPE html>
<html lang="en">
<head>
<meta charset="utf-8">
<title>RW Framewell Inc – Business Cards</title>
<link rel="stylesheet" href="https://fonts.googleapis.com/css2?family=Montserrat:wght@700&family=Raleway:wght@400;600&family=Roboto:wght@300&display=swap">
<style>
  :root {
    --brand-blue: #0077c8;
    --band-blue: #0a6fb8;
    --card-white: #f1f1f1;
    --ink-grey: #555555;
    --page-bg: #e4e4e4;
    --white: #ffffff;
  }
  * { margin: 0; padding: 0; box-sizing: border-box; }
  html, body {
    width: 1200px;
    height: 900px;
    overflow: hidden;
    background: var(--page-bg);
  }
  .sheet {
    position: relative;
    width: 1200px;
    height: 900px;
  }
  .card {
    position: absolute;
    left: 285px;
    width: 630px;
    height: 360px;
    box-shadow: 0 4px 14px rgba(0, 0, 0, 0.12);
    overflow: hidden;
  }
  .card-front {
    top: 70px;
    background: var(--brand-blue);
    display: flex;
    align-items: center;
    justify-content: center;
  }
  .wordmark {
    font-family: "Raleway", sans-serif;
    font-weight: 600;
    font-size: 46px;
    letter-spacing: 4px;
    color: var(--white);
  }
  .card-back {
    top: 470px;
    background: var(--card-white);
  }
  .identity {
    position: absolute;
    right: 350px;
    top: 140px;
    text-align: right;
  }
  .person-name {
    font-family: "Montserrat", sans-serif;
    font-weight: 700;
    font-size: 24px;
    color: var(--brand-blue);
    line-height: 1.1;
  }
  .person-title {
    font-family: "Raleway", sans-serif;
    font-weight: 400;
    font-size: 15px;
    color: var(--ink-grey);
    margin-top: 4px;
  }
  .divider {
    position: absolute;
    left: 314px;
    top: 150px;
    width: 2px;
    height: 60px;
    background: var(--brand-blue);
  }
  .contact-list {
    position: absolute;
    left: 348px;
    top: 146px;
    list-style: none;
  }
  .contact-item {
    display: flex;
    align-items: center;
    height: 23px;
    font-family: "Raleway", sans-serif;
    font-weight: 400;
    font-size: 14px;
    color: var(--ink-grey);
  }
  .contact-icon {
    width: 14px;
    height: 14px;
    margin-right: 10px;
    flex: none;
  }
  .address-band {
    position: absolute;
    left: 0;
    top: 279px;
    width: 100%;
    height: 31px;
    background: var(--band-blue);
    display: flex;
    align-items: center;
    justify-content: center;
    font-family: "Roboto", sans-serif;
    font-weight: 300;
    font-size: 16px;
    color: var(--white);
  }
</style>
</head>
<body>
<main class="sheet">
  <section class="card card-front">
    <span class="wordmark">RW FRAMEWELL</span>
  </section>

  <section class="card card-back">
    <div class="identity">
      <p class="person-name">DANA REEVES</p>
      <p class="person-title">FOUNDER</p>
    </div>
    <div class="divider"></div>
    <ul class="contact-list">
      <li class="contact-item">
        <svg class="contact-icon" viewBox="0 0 24 24" aria-hidden="true">
          <path fill="var(--brand-blue)" d="M6.6 10.8a15.1 15.1 0 0 0 6.6 6.6l2.2-2.2c.3-.3.7-.4 1-.2 1.1.4 2.3.6 3.6.6.6 0 1 .4 1 1V20c0 .6-.4 1-1 1A17 17 0 0 1 3 4c0-.6.4-1 1-1h3.5c.6 0 1 .4 1 1 0 1.3.2 2.5.6 3.6.1.3 0 .7-.2 1z"/>
        </svg>
        +000000000000
      </li>
      <li class="contact-item">
        <svg class="contact-icon" viewBox="0 0 24 24" aria-hidden="true">
          <rect x="2" y="5" width="20" height="14" fill="var(--brand-blue)"/>
          <path d="M2 5l10 8 10-8M2 19l7-7M22 19l-7-7" stroke="var(--white)" stroke-width="1.6" fill="none"/>
        </svg>
        INFO@YOURMAIL.COM
      </li>
      <li class="contact-item">
        <svg class="contact-icon" viewBox="0 0 24 24" aria-hidden="true">
          <circle cx="12" cy="12" r="10" fill="var(--brand-blue)"/>
          <path d="M2 12h20M12 2c3 3 3 17 0 20M12 2c-3 3-3 17 0 20" stroke="var(--white)" stroke-width="1.4" fill="none"/>
        </svg>
        WWW.YOURWEBSITE.COM
      </li>
    </ul>
    <div class="address-band">YOUR LOCATION STREET HERE-9100</div>
  </section>
</main>
</body>
</html>
```